BrivoTerna. Lantern of the Steady Harvest. Business card

Professional business card for BrivoTerna (Lantern of the Steady Harvest)
My rationale: Strategy-> Execution-> Results-> Value that lead to the BrivoTerna name: We put the Lantern of the Steady Harvest.
We deliver value to our customers helping them at defining a good strategy (cyan arrow). 90% of well formulated strategies fail due to poor execution so we also consider strategical execution very important (green arrow). Due to the execution we obtain the results (blue arrow). Finally, the results provide feedback to redefine strategy, and the new strategy has to be executed and new results obtained providing new feedback and on and on. It's like a wheel that finally, must create corporate value: value for shareholders, staholders, employees, providers...-

Target Market(s)

CEOs and steering comitees , invewrnent funds

Industry/Entity Type

Business Consultant

Contact Information for Business Card

Teodoro Vinsquel
CEO & Founder
teodoro.vinsquel@brivoterna-example.com
Mobile: +34 655.803.912
www.brivoterna-example.com

Colors

Designer to choose colors to be used in the design.

Requirements
Nice to have
• Nice to hace the words: Strategy, execution, results
• Nice to vave the claim: Lantern of the Steady Harvest
• The three colors should be shown:
• cyan for STRATEGY
• green for EXECUTION
• blue for RESULTS
Should not have
• Complete black background

```html
<!DOCTYPE html>
<html lang="en">
<head>
<meta charset="utf-8">
<title>BrivoTerna – Business Card</title>
<link href="https://fonts.googleapis.com/css2?family=Open+Sans:wght@400;700&display=swap" rel="stylesheet">
<style>
  :root {
    --bg: #e6e3df;
    --card: #ffffff;
    --navy: #0a2e8c;
    --blue: #1e5ba8;
    --green: #8cc63f;
    --cyan: #1bb1e7;
    --ink: #3a3a3a;
    --white: #ffffff;
  }
  * { margin: 0; padding: 0; box-sizing: border-box; }
  html, body {
    width: 1200px; height: 997px; overflow: hidden;
    background: var(--bg);
    font-family: "Open Sans", Arial, sans-serif;
  }
  .canvas {
    position: relative; width: 1200px; height: 997px;
    display: flex; align-items: center; justify-content: center; gap: 40px;
  }
  .card {
    position: relative; width: 540px; height: 310px;
    background: var(--card);
    box-shadow: 0 6px 18px rgba(0,0,0,0.12);
    overflow: hidden;
  }

  /* Front: contact side */
  .holder {
    position: absolute; top: 34px; right: 34px; text-align: right;
  }
  .holder-name { color: var(--navy); font-weight: 700; font-size: 17px; letter-spacing: 0.2px; }
  .holder-role { color: var(--cyan); font-size: 13px; margin-top: 1px; }
  .wordmark {
    position: absolute; display: flex; align-items: center; gap: 10px;
    color: var(--navy); font-weight: 700;
  }
  .front .wordmark { left: 34px; top: 104px; font-size: 38px; letter-spacing: -0.5px; }
  .mark-dot { width: 18px; height: 18px; border-radius: 50%; background: var(--cyan); flex: none; }
  .contact-list {
    position: absolute; left: 34px; bottom: 70px; list-style: none;
    font-size: 13px; color: var(--ink); line-height: 18px;
  }
  .contact-list li { display: flex; align-items: center; gap: 8px; }
  .contact-list svg { width: 11px; height: 11px; flex: none; }
  .stripe-set {
    position: absolute; left: 0; right: 0; bottom: 44px;
    display: flex; flex-direction: column;
  }
  .stripe { height: 3px; }
  .stripe-strategy { background: var(--cyan); }
  .stripe-execution { background: var(--green); }
  .stripe-results { background: var(--blue); }
  .pillar-band {
    position: absolute; left: 0; right: 0; bottom: 0; height: 44px;
    background: var(--navy);
    display: flex; align-items: center; justify-content: flex-end;
    padding: 0 34px;
    color: var(--white); font-weight: 700; font-size: 12px;
  }

  /* Back: brand side */
  .back .brand-block {
    position: absolute; inset: 0;
    display: flex; flex-direction: column; align-items: center; justify-content: center;
  }
  .back .wordmark { position: static; font-size: 50px; letter-spacing: -0.5px; }
  .back .mark-dot { width: 24px; height: 24px; }
  .claim {
    display: flex; align-items: center; gap: 10px; margin-top: 10px;
    color: var(--navy); font-size: 14px; letter-spacing: 0.3px;
  }
  .claim-rule { width: 70px; height: 1px; background: var(--cyan); }
</style>
</head>
<body>
<main class="canvas">

  <section class="card front" aria-label="Business card, contact side">
    <div class="holder">
      <p class="holder-name">Teodoro Vinsquel</p>
      <p class="holder-role">CEO &amp; Founder</p>
    </div>

    <div class="wordmark"><span class="mark-dot"></span>BrivoTerna</div>

    <ul class="contact-list">
      <li>
        <svg viewBox="0 0 12 12" aria-hidden="true"><rect x="3" y="0.5" width="6" height="11" rx="1.2" fill="none" stroke="var(--cyan)" stroke-width="1.3"/></svg>
        +34 655.803.912
      </li>
      <li>
        <svg viewBox="0 0 12 12" aria-hidden="true"><rect x="0.5" y="2" width="11" height="8" fill="var(--cyan)"/><path d="M0.5,2 L6,7 L11.5,2" fill="none" stroke="var(--white)" stroke-width="1"/></svg>
        teodoro.vinsquel@brivoterna-example.com
      </li>
      <li>
        <svg viewBox="0 0 12 12" aria-hidden="true"><circle cx="6" cy="6" r="5.3" fill="var(--cyan)"/><path d="M1,6 H11 M6,1 V11" stroke="var(--white)" stroke-width="0.8"/></svg>
        www.brivoterna-example.com
      </li>
    </ul>

    <div class="stripe-set" aria-hidden="true">
      <span class="stripe stripe-strategy"></span>
      <span class="stripe stripe-execution"></span>
      <span class="stripe stripe-results"></span>
    </div>
    <p class="pillar-band">Strategy - Execution - Results</p>
  </section>

  <section class="card back" aria-label="Business card, brand side">
    <div class="brand-block">
      <div class="wordmark"><span class="mark-dot"></span>BrivoTerna</div>
      <p class="claim"><span class="claim-rule"></span>Lantern of the Steady Harvest<span class="claim-rule"></span></p>
    </div>
  </section>

</main>
</body>
</html>
```